Paul Denton Sausage Label Design

Halvern Fields Corporation is seeking to create a new brand of fresh 100% Canadian pork sausage. This label will be a paper band that slips on and off foam trays. The front facing side will be 5 inches wide by 3.5 inches high. The following is some information about our brand.
Target market:
1. Working Moms
2. Stay at home moms
3. Barbeque enthusiast
Brand personality
1. Old school values – We are a family run company who believes in an honest days work
2. Modern day sensibility – We believe in being nimble and open to new ideas
3. Energetic and optimistic – We are passionate about our business and product
4. Relaxed sense of humor – We believe that it is possible to work hard and have fun
Positioning Statements:
Our sausage is the easy choice for adding flavour to your real- life family meals, that’s because:
1. It is 100% fresh Canadian product with no fillers or preservatives
2. It is a great tasting recipe with simple, natural ingredients
3. It is brought to you with good humor and integrity by a multi- generational family owned business
We are looking for a creative designer to make our ideas come to life. There are three types of designs we would like to see:
1. Rustic – a rustic, barbequing, old farm, country feel – without feeling too old
2. Modern & Simple – Very simple clean face with clean text
3. Family friendly – a label that would appeal to the everyday family with photos of the finished product
This brand does not have a name yet, please use the name “Paul Denton “as a place holder. Please keep in mind the information provided about our brand when developing the label. Attached are pictures of some ideas we like. Please do not copy these ideas too closely, we are looking to differentiate ourselves in the market. Samples are to provide some guidance of our preferences.
Target Market(s)
1. Working Moms
2. Stay at home moms
3. Barbeque enthusiast
Colors
Designer to choose colors to be used in the design.

```html
<!DOCTYPE html>
<html lang="en">
<head>
<meta charset="utf-8">
<title>Paul Denton – Mutton &amp; Mint Pork Sausages Label</title>
<link rel="stylesheet" href="https://fonts.googleapis.com/css2?family=Alfa+Slab+One&family=Arvo:wght@700&family=Yellowtail&display=block">
<style>
  :root {
    --label-green: #b8cf3d;
    --cream: #eef0dc;
    --forest: #274a1e;
    --sausage-tone: #d6dca4;
    --sausage-outline: #3a3a3a;
  }
  * { margin: 0; padding: 0; box-sizing: border-box; }
  html, body { width: 1200px; height: 843px; overflow: hidden; background: var(--label-green); }
  .label {
    position: relative;
    width: 1200px;
    height: 843px;
    background: var(--label-green);
    font-family: "Arvo", "Rockwell", serif;
    font-weight: 700;
    color: var(--cream);
  }
  .rules { position: absolute; inset: 0; }
  .txt { position: absolute; line-height: 1; white-space: nowrap; }

  .company { left: 50px; top: 70px; font-size: 24px; letter-spacing: 0.4px; }

  .brand-name {
    left: 40px;
    font-family: "Alfa Slab One", "Rockwell", serif;
    font-weight: 400;
    font-size: 92px;
    letter-spacing: -2px;
    color: var(--cream);
    text-shadow: 5px 5px 0 var(--forest);
    transform: scaleY(1.2);
    transform-origin: left top;
  }
  .brand-name.first { top: 166px; }
  .brand-name.last { top: 294px; }

  .product-art {
    position: absolute;
    left: 584px; top: 122px;
    width: 530px; height: 236px;
  }
  .origin-map {
    position: absolute;
    left: 64px; top: 486px;
    width: 176px; height: 184px;
  }

  .script { font-family: "Yellowtail", "Kaushan Script", cursive; font-weight: 400; }
  .origin-claim { left: 254px; top: 478px; font-size: 32px; line-height: 0.9; transform: rotate(-4deg); transform-origin: left top; }
  .natural-claim { left: 428px; top: 478px; font-size: 44px; }

  .flavour { left: 432px; top: 565px; font-size: 57px; color: var(--forest); letter-spacing: 1.5px; }
  .variety { left: 441px; top: 633px; font-size: 33px; }

  .count { left: 72px; top: 728px; font-size: 28px; }
  .weight { left: 194px; top: 720px; font-size: 33px; }
  .weight .estimated { font-family: "Georgia", serif; font-weight: 400; font-size: 42px; margin-left: 10px; }
  .storage { left: 194px; top: 760px; font-size: 16px; letter-spacing: 0.6px; }
  .description { left: 440px; top: 717px; font-size: 31.5px; line-height: 41px; letter-spacing: 1px; }
</style>
</head>
<body>
<main class="label">
  <svg class="rules" width="1200" height="843" aria-hidden="true">
    <g stroke="var(--cream)" stroke-width="3.2" fill="none">
      <line x1="46" y1="126" x2="509" y2="126"/>
      <line x1="510" y1="48" x2="510" y2="458"/>
      <line x1="42" y1="459" x2="1158" y2="459"/>
      <line x1="410" y1="461" x2="410" y2="798"/>
      <line x1="410" y1="544" x2="1158" y2="544"/>
      <line x1="42" y1="692" x2="1158" y2="692"/>
      <line x1="162" y1="694" x2="162" y2="798"/>
    </g>
  </svg>

  <div class="txt company">HALVERN FIELDS CORPORATION</div>
  <div class="txt brand-name first">PAUL</div>
  <div class="txt brand-name last">DENTON</div>

  <svg class="product-art" viewBox="0 0 530 236" role="img" aria-label="Illustration of a sausage in a bun">
    <rect x="4" y="4" width="522" height="228" rx="110" fill="var(--sausage-tone)" stroke="var(--sausage-outline)" stroke-width="6"/>
  </svg>

  <svg class="origin-map" viewBox="0 0 176 184" role="img" aria-label="Map of Canada">
    <rect x="0" y="0" width="176" height="184" rx="16" fill="var(--cream)" opacity="0.85"/>
  </svg>

  <div class="txt script origin-claim">100%<br>Canadian</div>
  <div class="txt script natural-claim">All Natural</div>

  <div class="txt flavour">MUTTON &amp; MINT</div>
  <div class="txt variety">PORK SAUSAGES</div>

  <div class="txt count">X6</div>
  <div class="txt weight">400G<span class="estimated">℮</span></div>
  <div class="txt storage">KEEP REFRIGERATED</div>
  <div class="txt description">6 MATURE MUTTON&nbsp; SAUSAGE,<br>INFUSED WITH MINT.</div>
</main>
</body>
</html>
```